Business Broker Graphics Package

Hi,

Seeking a smart and professional graphics package design including business card design (double-sided) and letterhead and PowerPoint slide template.

3 Deliverables:

1. Company Letterhead
2. Business Card (two sided) (will consider one sided designs)
3. PowerPoint Template. Requires cover PPT and 2nd page design.

For the prototype use this info:
Marcus Dellorane RPA
Registered Practice Adviser
5678 Harlow Rd.
Tampa, FL 77777
555.014.2273
Demo@Quillbrookpath.com
www.QuillbrookPath.com

I'll give exact information to winner to finalize later.

I've attached the logo..

Business card will be double sided and info for back of card is in attachment.

Look forward to your great ideas and concepts!

Target Market(s)

President's and business owners, CPA's and other professionals.

Industry/Entity Type

Business

Requirements
Nice to have
• Prefer horizontal card, but will consider vertical card design.

The business card should be all or primarily white. Text colors should be same as logo creative combination of black and forest green.

PowerPoint can be white background or lighter palette of colors I like gold color. I do not like darkly colored PowerPoint designs I prefer light and bright designs.

```html
<!DOCTYPE html>
<html lang="en">
<head>
<meta charset="utf-8">
<title>QuillbrookPath Stationery Package</title>
<link rel="stylesheet" href="https://fonts.googleapis.com/css2?family=Cinzel:wght@600&family=Roboto+Condensed:wght@400;500&family=Source+Sans+3:wght@400;700&display=swap">
<style>
  :root {
    --board: #8a8a8a;
    --paper: #ffffff;
    --forest: #0b3d24;
    --ink: #1d1d1b;
    --text-grey: #444444;
    --rule: #d4d4d4;
    --charcoal: #242424;
    --signature-tone: #e6e6e6;
  }
  * { box-sizing: border-box; margin: 0; padding: 0; }
  html, body { width: 1200px; height: 640px; overflow: hidden; }
  body { background: var(--board); position: relative; font-family: "Source Sans 3", sans-serif; color: var(--ink); }

  .sheet { position: absolute; background: var(--paper); overflow: hidden; }

  .brand-name { font-family: "Cinzel", serif; font-weight: 600; color: var(--ink); white-space: nowrap; letter-spacing: 0.3px; }

  .slant-tab {
    position: absolute; background: var(--forest); color: var(--paper);
    font-family: "Cinzel", serif; font-weight: 600; text-align: center;
    clip-path: polygon(6px 0, 100% 0, 100% 100%, 0 100%);
  }

  /* Letterhead */
  .letterhead { top: 22px; width: 300px; height: 386px; }
  .letterhead--first { left: 18px; }
  .letterhead--second { left: 336px; }
  .letterhead .brand-name { position: absolute; top: 24px; left: 0; width: 100%; text-align: center; font-size: 10px; }
  .recipient { position: absolute; top: 68px; left: 26px; font-size: 4px; line-height: 7px; }
  .recipient strong, .sign-off strong { font-weight: 700; }
  .letter-body { position: absolute; top: 105px; left: 26px; width: 248px; font-size: 3.7px; line-height: 8.8px; }
  .letter-body p { margin-bottom: 10px; }
  .signature { position: absolute; top: 296px; left: 26px; width: 95px; height: 20px; background: var(--signature-tone); }
  .sign-off { position: absolute; top: 318px; left: 26px; font-size: 4px; line-height: 7px; }
  .letter-contact { position: absolute; top: 350px; left: 26px; font-size: 3.8px; }
  .letterhead .slant-tab { left: 175px; top: 370px; width: 125px; height: 16px; font-size: 5.5px; line-height: 16px; }

  /* Presentation cover */
  .slide-cover { left: 714px; top: 27px; width: 376px; height: 282px; }
  .cover-field { position: absolute; left: 0; top: 0; width: 100%; height: 188px; background: var(--forest); }
  .cover-logo-band { position: absolute; left: 0; top: 188px; width: 100%; height: 55px; display: flex; align-items: center; justify-content: center; }
  .cover-logo-band .brand-name { font-size: 12px; margin-top: 12px; }
  .cover-footer { position: absolute; left: 0; top: 243px; width: 100%; height: 39px; background: var(--forest); color: var(--paper); text-align: center; }
  .section-title { font-family: "Cinzel", serif; font-weight: 600; letter-spacing: 0.3px; }
  .cover-footer .section-title { font-size: 8.5px; margin-top: 5px; }
  .service-list { list-style: none; display: flex; justify-content: center; gap: 4px; font-family: "Roboto Condensed", sans-serif; }
  .service-list li::before { content: ""; display: inline-block; width: 0.45em; height: 0.45em; background: currentColor; margin-right: 0.3em; vertical-align: 0.12em; }
  .cover-footer .service-list { font-size: 8px; margin-top: 2px; }

  /* Presentation inner page */
  .slide-inner { left: 714px; top: 344px; width: 376px; height: 280px; }
  .slide-inner .brand-name { position: absolute; left: 17px; top: 26px; font-size: 8.5px; }
  .inner-band { position: absolute; left: 0; top: 269px; width: 218px; height: 11px; background: var(--charcoal); clip-path: polygon(0 0, 100% 0, calc(100% - 6px) 100%, 0 100%); }
  .slide-inner .slant-tab { left: 222px; top: 259px; width: 154px; height: 21px; font-family: "Source Sans 3", sans-serif; font-weight: 400; font-size: 5px; line-height: 21px; }

  /* Business card front */
  .card-front { left: 18px; top: 434px; width: 304px; height: 178px; }
  .card-front .brand-name { position: absolute; left: 24px; top: 50px; font-size: 14px; }
  .card-holder { position: absolute; left: 184px; top: 59px; font-family: "Roboto Condensed", sans-serif; color: var(--text-grey); }
  .card-holder .person-name { font-size: 12px; font-weight: 400; }
  .card-holder .person-role { font-size: 7.5px; margin-top: 3px; color: var(--ink); }
  .card-rule { position: absolute; left: 24px; top: 85px; width: 262px; height: 1px; background: var(--rule); }
  .contact-list { position: absolute; left: 17px; top: 92px; list-style: none; font-family: "Roboto Condensed", sans-serif; font-size: 8.6px; color: var(--text-grey); }
  .contact-list li { display: flex; align-items: center; height: 13.5px; }
  .contact-icon { width: 10px; height: 10px; margin-right: 5px; flex: none; }
  .card-front .slant-tab { left: 182px; top: 161px; width: 122px; height: 17px; font-size: 6.5px; line-height: 17px; }

  /* Business card back */
  .card-back { left: 336px; top: 434px; width: 304px; height: 178px; }
  .card-back .brand-name { position: absolute; left: 30px; top: 10px; font-size: 11px; transform-origin: 0 0; transform: rotate(90deg); }
  .back-band { position: absolute; left: 0; top: 128px; width: 100%; height: 50px; background: var(--forest); color: var(--paper); text-align: center; }
  .back-band .section-title { font-size: 9px; margin-top: 9px; }
  .back-band .service-list { font-size: 8px; margin-top: 3px; }
</style>
</head>
<body>

  <!-- Letterhead, version one -->
  <section class="sheet letterhead letterhead--first" aria-label="Letterhead">
    <div class="brand-name">QuillbrookPath</div>
    <div class="recipient">
      <div>To</div>
      <div><strong>The Lorem Ipsum</strong></div>
      <div>Sample text for printing and typesetting industry</div>
    </div>
    <div class="letter-body">
      <p>Lorem Ipsum is simply dummy text of the printing and typesetting industry. Lorem Ipsum has been the industry's standard dummy text ever since the 1500s, when an unknown printer took a galley of type and scrambled it to make a type specimen book. It has survived not only five centuries, but also the leap into electronic typesetting, remaining essentially unchanged. It was popularised in the 1960s with the release of Lettrane sheets containing Lorem Ipsum passages, and more recently with desktop publishing software like Pressmark Layout including versions of Lorem Ipsum.</p>
      <p>It is a long established fact that a reader will be distracted by the readable content of a page when looking at its layout. The point of using Lorem Ipsum is that it has a more-or-less normal distribution of letters, as opposed to using 'Content here, content here', making it look like readable English. Many desktop publishing packages and web page editors now use Lorem Ipsum as their default model text, and a search for 'lorem ipsum' will uncover many web sites still in their infancy. Various versions have evolved over the years, sometimes by accident, sometimes on purpose (injected humour and the It is a long established fact that a reader will be distracted by the readable content of a page when looking at its layout. The point of using Lorem Ipsum is that it has a more-or-less normal distribution of letters, as opposed to using 'Content here, content here', making it look like readable English. Many desktop publishing packages and web page editors now use Lorem Ipsum as their default model text, and a search for 'lorem ipsum' will uncover many web sites still in their infancy.</p>
      <p>It is a long established fact that a reader will be distracted by the readable content of a page when looking at its layout. The point of using Lorem Ipsum is that it has a more-or-less normal distribution of letters, as opposed to using 'Content here, content here', making it look like readable English. Many desktop publishing packages and web page editors now use Lorem Ipsum as their default model text, and a search for 'lorem ipsum' will uncover many web sites still in their infancy. Various versions have evolved over the years, sometimes by accident, sometimes on purpose.</p>
    </div>
    <div class="signature" role="img" aria-label="Handwritten signature"></div>
    <div class="sign-off">
      <div><strong>The Lorem Ipsum</strong></div>
      <div>Sample text for printing and typesetting industry</div>
    </div>
    <div class="letter-contact">555.014.2273 | www.QuillbrookPath.com</div>
    <div class="slant-tab">Ownership Solutions</div>
  </section>

  <!-- Letterhead, version two -->
  <section class="sheet letterhead letterhead--second" aria-label="Letterhead alternate">
    <div class="brand-name">QuillbrookPath</div>
    <div class="recipient">
      <div>To</div>
      <div><strong>The Lorem Ipsum</strong></div>
      <div>Sample text for printing and typesetting industry</div>
    </div>
    <div class="letter-body">
      <p>Lorem Ipsum is simply dummy text of the printing and typesetting industry. Lorem Ipsum has been the industry's standard dummy text ever since the 1500s, when an unknown printer took a galley of type and scrambled it to make a type specimen book. It has survived not only five centuries, but also the leap into electronic typesetting, remaining essentially unchanged. It was popularised in the 1960s with the release of Lettrane sheets containing Lorem Ipsum passages, and more recently with desktop publishing software like Pressmark Layout including versions of Lorem Ipsum.</p>
      <p>It is a long established fact that a reader will be distracted by the readable content of a page when looking at its layout. The point of using Lorem Ipsum is that it has a more-or-less normal distribution of letters, as opposed to using 'Content here, content here', making it look like readable English. Many desktop publishing packages and web page editors now use Lorem Ipsum as their default model text, and a search for 'lorem ipsum' will uncover many web sites still in their infancy. Various versions have evolved over the years, sometimes by accident, sometimes on purpose (injected humour and the It is a long established fact that a reader will be distracted by the readable content of a page when looking at its layout. The point of using Lorem Ipsum is that it has a more-or-less normal distribution of letters, as opposed to using 'Content here, content here', making it look like readable English. Many desktop publishing packages and web page editors now use Lorem Ipsum as their default model text, and a search for 'lorem ipsum' will uncover many web sites still in their infancy.</p>
      <p>It is a long established fact that a reader will be distracted by the readable content of a page when looking at its layout. The point of using Lorem Ipsum is that it has a more-or-less normal distribution of letters, as opposed to using 'Content here, content here', making it look like readable English. Many desktop publishing packages and web page editors now use Lorem Ipsum as their default model text, and a search for 'lorem ipsum' will uncover many web sites still in their infancy. Various versions have evolved over the years, sometimes by accident, sometimes on purpose.</p>
    </div>
    <div class="signature" role="img" aria-label="Handwritten signature"></div>
    <div class="sign-off">
      <div><strong>The Lorem Ipsum</strong></div>
      <div>Sample text for printing and typesetting industry</div>
    </div>
    <div class="letter-contact">555.014.2273 | www.QuillbrookPath.com</div>
    <div class="slant-tab">Ownership Solutions</div>
  </section>

  <!-- Presentation cover slide -->
  <section class="sheet slide-cover" aria-label="Presentation cover slide">
    <div class="cover-field"></div>
    <div class="cover-logo-band"><div class="brand-name">QuillbrookPath</div></div>
    <div class="cover-footer">
      <div class="section-title">Ownership Solutions</div>
      <ul class="service-list">
        <li>Business Sale</li><li>Acquisition</li><li>Exit Planning</li><li>Valuation</li><li>Growth Engineering</li>
      </ul>
    </div>
  </section>

  <!-- Presentation inner slide -->
  <section class="sheet slide-inner" aria-label="Presentation content slide">
    <div class="brand-name">QuillbrookPath</div>
    <div class="inner-band"></div>
    <div class="slant-tab">555.014.2273 | www.QuillbrookPath.com</div>
  </section>

  <!-- Business card front -->
  <section class="sheet card-front" aria-label="Business card front">
    <div class="brand-name">QuillbrookPath</div>
    <div class="card-holder">
      <div class="person-name">Marcus Dellorane RPA</div>
      <div class="person-role">Registered Practice Adviser</div>
    </div>
    <div class="card-rule"></div>
    <ul class="contact-list">
      <li>
        <svg class="contact-icon" viewBox="0 0 10 10" aria-hidden="true"><rect width="10" height="10" rx="1.5" fill="#0b3d24"/><rect x="3.2" y="1.8" width="3.6" height="6.4" rx="0.7" fill="none" stroke="#fff" stroke-width="0.8"/><circle cx="5" cy="7.1" r="0.4" fill="#fff"/></svg>
        555.014.2273
      </li>
      <li>
        <svg class="contact-icon" viewBox="0 0 10 10" aria-hidden="true"><rect width="10" height="10" rx="1.5" fill="#0b3d24"/><path d="M5 8.6 C3.2 6.4 2.6 5.3 2.6 4.2 A2.4 2.4 0 0 1 7.4 4.2 C7.4 5.3 6.8 6.4 5 8.6Z" fill="#fff"/><circle cx="5" cy="4.2" r="0.9" fill="#0b3d24"/></svg>
        5678 Harlow Rd. Tampa, FL 77777
      </li>
      <li>
        <svg class="contact-icon" viewBox="0 0 10 10" aria-hidden="true"><rect width="10" height="10" rx="1.5" fill="#0b3d24"/><rect x="1.8" y="2.8" width="6.4" height="4.4" fill="#fff"/><path d="M1.8 2.8 L5 5.4 L8.2 2.8" fill="none" stroke="#0b3d24" stroke-width="0.7"/></svg>
        Demo@Quillbrookpath.com
      </li>
      <li>
        <svg class="contact-icon" viewBox="0 0 10 10" aria-hidden="true"><rect width="10" height="10" rx="1.5" fill="#0b3d24"/><circle cx="5" cy="5" r="3" fill="none" stroke="#fff" stroke-width="0.7"/><ellipse cx="5" cy="5" rx="1.3" ry="3" fill="none" stroke="#fff" stroke-width="0.6"/><path d="M2 5 H8" stroke="#fff" stroke-width="0.6"/></svg>
        www.QuillbrookPath.com
      </li>
    </ul>
    <div class="slant-tab">Ownership Solutions</div>
  </section>

  <!-- Business card back -->
  <section class="sheet card-back" aria-label="Business card back">
    <div class="brand-name">QuillbrookPath</div>
    <div class="back-band">
      <div class="section-title">Ownership Solutions</div>
      <ul class="service-list">
        <li>Business Sale</li><li>Acquisition</li><li>Exit Planning</li><li>Valuation</li><li>Growth Engineering</li>
      </ul>
    </div>
  </section>

</body>
</html>
```